Veltrano.co - Polar Expeditions Specialists

We need a modern, visually striking business card for Veltrano.co, a company specialized in selling expedition cruises to the most remote regions on Earth, with a focus on the Arctic and Antarctica. The design should instantly communicate that the cardholder is an expert in polar travel. Use clean, premium aesthetics with cool tones like icy blue and white, possibly incorporating polar imagery (ice, glaciers, penguins, etc.)

Attached the logo

Contact Information for Business Card

Feels high-end and trustworthy.. Visually memorable — encourages people to keep it

Colors
0054AA
0677BA
7BADD7
CADEEF
E8F1F8

Requirements
Must have
• ice, glaciers, penguins, montains
Nice to have
• modern, transparente,

```html
<!DOCTYPE html>
<html lang="en">
<head>
<meta charset="utf-8">
<title>Veltrano.co – Business Card</title>
<link href="https://fonts.googleapis.com/css2?family=Poppins:wght@400;500;600;700&display=swap" rel="stylesheet">
<style>
  :root {
    --page-bg: #6b6b6b;
    --brand-blue: #2f73b9;
    --deep-blue: #0054aa;
    --mid-blue: #4a86c5;
    --soft-blue: #7badd7;
    --ice: #e8f1f8;
    --ice-2: #cadeef;
    --ink: #2b2b2b;
    --white: #ffffff;
  }
  * { box-sizing: border-box; margin: 0; padding: 0; }
  html, body { width: 1093px; height: 1200px; overflow: hidden; }
  body {
    background: var(--page-bg);
    font-family: "Poppins", sans-serif;
    position: relative;
  }
  .card {
    position: absolute;
    left: 265px;
    width: 579px;
    height: 356px;
    border-radius: 24px;
    overflow: hidden;
    box-shadow: 3px 5px 6px rgba(0,0,0,0.55);
  }
  .card--front { top: 226px; background: var(--white); }
  .card--back { top: 621px; }

  .scene {
    position: absolute; inset: 0;
  }
  .card--front .scene {
    background:
      linear-gradient(180deg, rgba(255,255,255,0) 70%, rgba(232,241,248,0.9) 100%),
      linear-gradient(100deg, #e4e7ea 0%, #f4f5f7 30%, #f7f8fa 60%, #eef1f4 100%);
  }
  .card--back .scene {
    background:
      linear-gradient(180deg, #5b92cc 0%, #4a82c0 45%, #4f89c7 75%, #5a93ce 100%);
  }
  .base-band {
    position: absolute; left: 0; right: 0; bottom: 0; height: 9px;
    background: var(--brand-blue);
  }

  .brand { position: absolute; text-align: center; }
  .brand__dot { display: block; margin: 0 auto; border-radius: 50%; }
  .brand__name { font-weight: 700; letter-spacing: -0.5px; line-height: 1; }
  .brand__tagline { font-weight: 500; line-height: 1; }

  .card--front .brand { left: 30px; width: 250px; top: 108px; }
  .card--front .brand__dot { width: 58px; height: 58px; background: var(--brand-blue); margin-bottom: 22px; }
  .card--front .brand__name { font-size: 40px; color: var(--brand-blue); }
  .card--front .brand__tagline { font-size: 12.5px; color: var(--brand-blue); margin-top: 9px; }

  .divider {
    position: absolute; left: 288px; top: 74px; width: 1px; height: 208px;
    background: #9aa0a6;
  }

  .holder { position: absolute; left: 311px; top: 88px; color: var(--ink); }
  .holder__name { font-size: 23px; font-weight: 600; color: var(--brand-blue); line-height: 1.05; }
  .holder__role { font-size: 17px; font-weight: 400; line-height: 1.1; }
  .contact { list-style: none; margin-top: 17px; }
  .contact li { display: flex; align-items: center; font-size: 17px; line-height: 21px; }
  .contact svg { width: 15px; height: 15px; margin-right: 7px; fill: var(--brand-blue); }
  .contact .accent { color: var(--brand-blue); }
  .address { margin-top: 14px; font-size: 17px; line-height: 21px; }

  .card--back .brand { left: 0; right: 0; top: 86px; }
  .card--back .brand__dot { width: 74px; height: 74px; background: var(--white); margin-bottom: 40px; }
  .card--back .brand__name { font-size: 52px; color: var(--white); }
  .card--back .brand__tagline { font-size: 16.5px; color: var(--white); margin-top: 10px; }
</style>
</head>
<body>

<section class="card card--front">
  <div class="scene" role="img" aria-label="Faded photo of a penguin on snow with icebergs behind"></div>
  <div class="brand">
    <span class="brand__dot"></span>
    <div class="brand__name">Veltrano.co</div>
    <div class="brand__tagline">Polar Expeditions Specialists</div>
  </div>
  <div class="divider"></div>
  <div class="holder">
    <div class="holder__name">Marek Halvorsen</div>
    <div class="holder__role">Managing Director</div>
    <ul class="contact">
      <li><svg viewBox="0 0 24 24"><path d="M6.6 10.8a15.1 15.1 0 0 0 6.6 6.6l2.2-2.2a1 1 0 0 1 1-.25 11.4 11.4 0 0 0 3.6.57 1 1 0 0 1 1 1V20a1 1 0 0 1-1 1A17 17 0 0 1 3 4a1 1 0 0 1 1-1h3.5a1 1 0 0 1 1 1c0 1.25.2 2.45.57 3.57a1 1 0 0 1-.25 1z"/></svg>055-318 274 906</li>
      <li><svg viewBox="0 0 24 24"><path d="M2 5h20v14H2z M2 5l10 8 10-8" fill="none" stroke="#2f73b9" stroke-width="2"/><path d="M2 5h20l-10 8z"/></svg>hello@veltranomail.com</li>
      <li><svg viewBox="0 0 24 24"><circle cx="12" cy="12" r="9.5" fill="none" stroke="#2f73b9" stroke-width="2"/><ellipse cx="12" cy="12" rx="4" ry="9.5" fill="none" stroke="#2f73b9" stroke-width="1.6"/><path d="M3 9h18M3 15h18" stroke="#2f73b9" stroke-width="1.6"/></svg>www.<span class="accent">veltranotrips</span>.com</li>
    </ul>
    <div class="address">87, Harbour Quay Road<br>30918, Northland</div>
  </div>
  <div class="base-band"></div>
</section>

<section class="card card--back">
  <div class="scene" role="img" aria-label="Blue-toned photo of a penguin walking on snow with mountains and sea behind"></div>
  <div class="brand">
    <span class="brand__dot"></span>
    <div class="brand__name">Veltrano.co</div>
    <div class="brand__tagline">Polar Expeditions Specialists</div>
  </div>
</section>

</body>
</html>
```